Brookvale Building Company - advertisement poster

I am looking to print some canvas signs to advertise my general contracting company, Brookvale Building Company. The sign will measure 6' long x 3' high so the size should match that ratio. I already have a logo icon, which is the Letter 'B' and some trees that I would like to incorporate, see attached. I would also like the to have the following information listed:
1) phone number: 831-555-0172
2) email: brookvalebuildingcompany@mailnest.example
3) website: brookvalebuildingcompany.example
4) Lic#4826130
5) I want to use this text: "BUILD WITH THE B-CREW!"

The ad should be relatively simple and clean. Black and Green are my company colors. I am open to creative ideas!

Target Market(s)

People looking to renovate their homes

Industry/Entity Type

Construction

Colors
59FF00
82FF00
B8FF75
E3FFCB
F4FFEA

Requirements
Must have
• Must have my company logo
Should not have
• No photos or complex graphics

```html
<!DOCTYPE html>
<html lang="en">
<head>
<meta charset="utf-8">
<title>Brookvale Building Company – Sign</title>
<link rel="stylesheet" href="https://fonts.googleapis.com/css2?family=Krona+One&family=Poppins:wght@400;600&display=swap">
<style>
  :root {
    --backdrop: #807d7e;
    --sign-black: #000000;
    --sign-white: #ffffff;
    --brand-green: #6cb43a;
    --ink: #111111;
  }
  html, body {
    margin: 0;
    padding: 0;
    width: 1200px;
    height: 730px;
    overflow: hidden;
    background: var(--backdrop);
  }
  .sign {
    position: absolute;
    left: 20px;
    top: 75px;
    width: 1160px;
    height: 580px;
    display: block;
  }
  .display { font-family: "Krona One", sans-serif; }
  .body-text { font-family: "Poppins", sans-serif; }
  .headline-green { fill: var(--brand-green); }
  .headline-white { fill: var(--sign-white); }
  .brand-name { fill: var(--sign-white); }
  .phone-number { fill: var(--sign-white); }
  .contact-line { fill: var(--ink); font-size: 36px; }
  .contact-bold { font-weight: 600; }
  .license-label, .license-number { fill: var(--ink); }
</style>
</head>
<body>
<svg class="sign" viewBox="0 0 1483 742" xmlns="http://www.w3.org/2000/svg" aria-label="Brookvale Building Company sign">
  <!-- panels -->
  <rect class="panel-top" x="0" y="0" width="1483" height="435" fill="var(--sign-black)"/>
  <rect class="panel-bottom" x="0" y="435" width="1483" height="307" fill="var(--sign-white)"/>

  <!-- headline -->
  <text class="display headline-green" x="70" y="182" font-size="118" textLength="969" lengthAdjust="spacingAndGlyphs">BUILD WITH</text>
  <text class="display headline-green" transform="translate(108 344) rotate(-90)" font-size="48" textLength="134" lengthAdjust="spacingAndGlyphs">THE</text>
  <text class="display headline-white" x="130" y="337" font-size="160" textLength="837" lengthAdjust="spacingAndGlyphs">B-CREW!</text>

  <!-- brand name -->
  <rect class="brand-square" x="1166" y="100" width="110" height="110" fill="var(--brand-green)"/>
  <text class="display brand-name" x="1043" y="290" font-size="44" textLength="350" lengthAdjust="spacingAndGlyphs">BROOKVALE</text>
  <text class="display brand-name" x="1046" y="320" font-size="18" textLength="346" lengthAdjust="spacingAndGlyphs">BUILDING COMPANY</text>

  <!-- phone bar -->
  <rect class="phone-bar-frame" x="67" y="379" width="1347" height="131" rx="32" fill="var(--sign-white)"/>
  <rect class="phone-bar" x="75" y="387" width="1332" height="120" rx="26" fill="var(--brand-green)"/>
  <circle class="phone-icon-disc" cx="141" cy="450" r="42" fill="var(--sign-black)"/>
  <path class="phone-icon" transform="translate(141 450)" fill="var(--brand-green)"
        d="M-17,-20 L-9,-25 L-2,-12 L-7,-7 Q-3,4 8,9 L13,4 L25,11 L20,19 Q-10,22 -17,-20 Z"/>
  <text class="display phone-number" x="214" y="490" font-size="120" textLength="1128" lengthAdjust="spacingAndGlyphs">831-555-0172</text>

  <!-- contact lines -->
  <g class="email-icon">
    <circle cx="88" cy="568" r="18" fill="var(--brand-green)"/>
    <rect x="77" y="561" width="22" height="15" rx="1.5" fill="none" stroke="var(--sign-white)" stroke-width="2"/>
    <path d="M77,562 L88,571 L99,562" fill="none" stroke="var(--sign-white)" stroke-width="2"/>
  </g>
  <text class="body-text contact-line" x="130" y="580" textLength="840" lengthAdjust="spacingAndGlyphs">brookvalebuildingcompany@mailnest.example</text>

  <g class="web-icon" fill="none" stroke="var(--sign-white)" stroke-width="2">
    <circle cx="88" cy="642" r="18" fill="var(--brand-green)" stroke="none"/>
    <circle cx="88" cy="642" r="10"/>
    <ellipse cx="88" cy="642" rx="4.5" ry="10"/>
    <line x1="78" y1="642" x2="98" y2="642"/>
  </g>
  <text class="body-text contact-line" x="130" y="653" textLength="840" lengthAdjust="spacingAndGlyphs">www.<tspan class="contact-bold">brookvalebuildingcompany</tspan>.example</text>

  <!-- license -->
  <rect class="license-box" x="977" y="538" width="425" height="130" rx="3" fill="var(--brand-green)"/>
  <rect class="license-label-field" x="982" y="543" width="415" height="52" fill="var(--sign-white)"/>
  <text class="display license-label" x="1017" y="584" font-size="38" textLength="342" lengthAdjust="spacingAndGlyphs">LICENSE NO.</text>
  <text class="display license-number" x="1020" y="650" font-size="50" textLength="322" lengthAdjust="spacingAndGlyphs">#4826130</text>
</svg>
</body>
</html>
```